Animal Eye Clinic needs a Business card

We are a new veterinary ophthalmology practice (Ridgeline Pet Vision Care) and we need a business card designed. We only see animal eyes - we are not a regular veterinary clinic. We already have a logo. We are looking for a professional, good looking business card to hand out to our clients. We are looking for something simple but professional and contemporary. Our logo is likely the only picture/graphic that needs to be on the card.
Updates

Contact Information for Business Card

Delia Vossman, BSc, DVM, MSc, DipACVO
Veterinary Ophthalmologist

Phone: 250.418.3927
Email: ridgelinepetvisioncare@mailbox-example.net
Website: ridgelinepetvisioncare-example.net
Address: 1874 Thornbury Rd
Kelowna, BC, V1X 4M9

Colors

Designer to choose colors to be used in the design.

Requirements
Must have
• Our logo (attached)

```html
<!DOCTYPE html>
<html lang="en">
<head>
<meta charset="utf-8">
<title>Ridgeline Pet Vision Care — Business Card</title>
<link rel="stylesheet" href="https://fonts.googleapis.com/css2?family=Montserrat:wght@700;800&family=Open+Sans:wght@400;600&display=swap">
<style>
  :root {
    --stage: #2b2b2b;
    --card: #1c1c1d;
    --teal: #1199aa;
    --white: #ffffff;
    --soft: #e9e9e9;
  }
  * { box-sizing: border-box; margin: 0; padding: 0; }
  html, body { width: 1200px; height: 895px; overflow: hidden; }
  body {
    background: var(--stage);
    font-family: "Open Sans", Arial, sans-serif;
    color: var(--white);
    position: relative;
  }
  .card {
    position: absolute;
    left: 290px;
    width: 620px;
    height: 354px;
    background: var(--card);
    border-radius: 22px;
    overflow: hidden;
    box-shadow: 0 10px 30px rgba(0,0,0,.45);
  }
  .card--front { top: 70px; }
  .card--back  { top: 471px; }

  /* Front */
  .brand {
    position: absolute;
    inset: 0;
    display: flex;
    align-items: center;
    justify-content: center;
    gap: 18px;
  }
  .brand__dot {
    width: 62px; height: 62px;
    border-radius: 50%;
    background: var(--teal);
    flex: none;
  }
  .brand__name {
    font-family: "Montserrat", Arial, sans-serif;
    font-weight: 800;
    font-size: 30px;
    line-height: 1.1;
    color: var(--teal);
    text-transform: uppercase;
    letter-spacing: .5px;
  }

  /* Back */
  .back__band { position: absolute; right: 0; top: 0; width: 330px; height: 354px; }
  .back__mark {
    position: absolute;
    right: 48px; top: 64px;
    width: 200px;
    display: flex; flex-direction: column; align-items: center; gap: 14px;
  }
  .back__mark .brand__dot { width: 110px; height: 110px; background: var(--teal); }
  .back__mark .brand__name { font-size: 17px; text-align: center; }

  .person { position: absolute; left: 34px; top: 40px; }
  .person__name {
    font-family: "Montserrat", Arial, sans-serif;
    font-weight: 800;
    font-size: 27px;
    color: var(--teal);
    text-transform: uppercase;
    line-height: 1.05;
  }
  .person__creds, .person__title { font-size: 14px; line-height: 1.3; color: var(--soft); }
  .person__creds { margin-top: 4px; }

  .contact { position: absolute; left: 34px; bottom: 30px; font-size: 13.5px; line-height: 1.45; color: var(--soft); }
  .contact__address { margin-bottom: 4px; }
  .contact__row { display: flex; align-items: center; gap: 10px; }
  .contact__icon { width: 15px; height: 15px; flex: none; }
</style>
</head>
<body>

<section class="card card--front" aria-label="Card front">
  <div class="brand">
    <span class="brand__dot"></span>
    <span class="brand__name">Ridgeline Pet<br>Vision Care</span>
  </div>
</section>

<section class="card card--back" aria-label="Card back">
  <svg class="back__band" viewBox="0 0 330 354" aria-hidden="true">
    <path d="M110 0 H330 V300 C250 330 140 330 60 300 C40 180 60 70 110 0 Z" fill="var(--teal)"/>
    <path d="M140 0 H330 V270 C250 292 160 290 95 268 C88 160 100 70 140 0 Z" fill="var(--white)"/>
  </svg>
  <div class="back__mark">
    <span class="brand__dot"></span>
    <span class="brand__name">Ridgeline Pet Vision Care</span>
  </div>

  <div class="person">
    <h1 class="person__name">Delia Vossman</h1>
    <p class="person__creds">BSc, DVM, MSc, DipACVO</p>
    <p class="person__title">Veterinary Ophthalmologist</p>
  </div>

  <div class="contact">
    <p class="contact__address">1874 Thornbury Rd<br>Kelowna, BC, V1X 4M9</p>
    <p class="contact__row">
      <svg class="contact__icon" viewBox="0 0 16 16" aria-hidden="true"><path d="M4 1.5l2.3 3-1.4 1.6c.8 1.8 2.2 3.3 4 4.1l1.6-1.4 3 2.3-1.3 2.4C7.3 13.5 2.5 8.7 1.6 2.8z" fill="var(--teal)"/></svg>
      250.418.3927
    </p>
    <p class="contact__row">
      <svg class="contact__icon" viewBox="0 0 16 16" aria-hidden="true"><rect x="1.5" y="3.5" width="13" height="9" rx="1" fill="none" stroke="var(--teal)" stroke-width="1.5"/><path d="M2 4l6 5 6-5" fill="none" stroke="var(--teal)" stroke-width="1.5"/></svg>
      ridgelinepetvisioncare@mailbox-example.net
    </p>
    <p class="contact__row">
      <svg class="contact__icon" viewBox="0 0 16 16" aria-hidden="true"><g fill="none" stroke="var(--teal)" stroke-width="1.3"><circle cx="8" cy="8" r="6.5"/><ellipse cx="8" cy="8" rx="3" ry="6.5"/><path d="M1.5 8h13M2.5 4.8h11M2.5 11.2h11"/></g></svg>
      ridgelinepetvisioncare-example.net
    </p>
  </div>
</section>

</body>
</html>
```